Meadowlight Soaps Business Card

The new business card design will incorporate my new logo components designed by one of your designers. Meadowlight Soaps creates high quality soaps and bath products. They would be suited for a Spa, Bed and Breakfast, Boutique environment. The look should be a white background.
Classy, soft and using the colour palet of the logo. The card will be two sided.

Reason: Need more time to make some changes and decide.

Target Market(s)

Looking to appeal to an upper end market. Spas, boutiques, independent gift stores, bridal salons, bed and breakfast, etc. I want the card to impart a sense of elegance, tranquility and Meadowlight. But also quality and value.

Industry/Entity Type

Business

Font styles to use
Sans Serif
Script

Requirements
Must have
• My logo on the front. But also on the back but faded out to allow written notes on the back.
On the front : Carol Pritchett
Owner/Creator
48 Fenwick Rd
Guelph, Ont N4K 2P9
519.402.6183
Creating Quality Handcrafted Soaps And Bath Products
Custom and Wholesale Orders Welcome
Www.meadowlightsoaps.ca
Www.friendpage.com / MeadowlightSoapandBath
info@meadowlightsoaps.ca

```html
<!DOCTYPE html>
<html lang="en">
<head>
<meta charset="utf-8">
<title>Meadowlight Soaps Business Card</title>
<link rel="stylesheet" href="https://fonts.googleapis.com/css2?family=Lato:wght@400;700;900&family=Pinyon+Script&display=swap">
<style>
  :root {
    --page: #e9e9e7;
    --card: #fbfbfa;
    --teal: #7fb2a5;
    --teal-dark: #5f9a8b;
    --teal-faint: #d6e6e1;
    --sand: #e4d7c9;
    --ink: #4d4d4d;
  }
  * { margin: 0; padding: 0; box-sizing: border-box; }
  html, body { width: 1200px; height: 997px; overflow: hidden; }
  body {
    background: var(--page);
    font-family: "Lato", sans-serif;
    color: var(--ink);
    position: relative;
  }
  .card {
    position: absolute;
    left: 250px;
    width: 700px;
    height: 400px;
    background: var(--card);
    box-shadow: 0 8px 24px rgba(0,0,0,.12);
    overflow: hidden;
  }
  .card--back { top: 70px; }
  .card--front { top: 527px; }
  .card__trim { position: absolute; left: 0; bottom: 0; width: 700px; height: 60px; }

  /* back */
  .faded-mark {
    position: absolute; left: 240px; top: 90px;
    display: flex; align-items: center; gap: 18px;
    color: var(--teal-faint);
    font-weight: 400; font-size: 44px;
  }
  .faded-mark__dot { width: 46px; height: 46px; border-radius: 50%; background: var(--teal-faint); }
  .notes { position: absolute; left: 56px; top: 200px; width: 560px; }
  .notes__title {
    font-weight: 700; font-size: 20px; text-decoration: underline;
    color: var(--ink); margin-bottom: 14px;
  }
  .notes__line { border-bottom: 3px dotted var(--teal); height: 34px; }

  /* front */
  .brand {
    position: absolute; left: 40px; top: 80px; width: 270px;
    text-align: center;
  }
  .brand__mark {
    display: flex; align-items: center; justify-content: center; gap: 10px;
    color: var(--teal); font-size: 30px; font-weight: 400; line-height: 1.1;
  }
  .brand__dot { width: 22px; height: 22px; border-radius: 50%; background: var(--teal); flex: none; }
  .brand__tagline {
    margin-top: 88px; color: var(--teal); font-weight: 900; font-size: 19px; line-height: 1.3;
  }
  .divider { position: absolute; left: 342px; top: 48px; width: 3px; height: 250px; background: var(--teal); }
  .person { position: absolute; left: 380px; top: 46px; }
  .person__name { font-family: "Pinyon Script", cursive; font-size: 46px; color: var(--teal); line-height: 1; }
  .person__role { font-size: 12px; font-weight: 700; letter-spacing: .5px; margin: 4px 0 0 70px; }
  .contact { position: absolute; left: 380px; top: 168px; list-style: none; }
  .contact__item { display: flex; align-items: center; gap: 10px; font-size: 15px; height: 34px; }
  .contact__icon { width: 22px; height: 22px; flex: none; }
</style>
</head>
<body>

<section class="card card--back" aria-label="Card back">
  <div class="faded-mark"><span class="faded-mark__dot"></span>Meadowlight Soaps</div>
  <div class="notes">
    <p class="notes__title">Notes</p>
    <div class="notes__line"></div>
    <div class="notes__line"></div>
    <div class="notes__line"></div>
    <div class="notes__line"></div>
  </div>
  <svg class="card__trim" viewBox="0 0 700 60" aria-hidden="true">
    <path d="M0 44 L700 44 L700 60 L0 60 Z" fill="var(--sand)"/>
    <path d="M520 44 C560 44 570 8 620 8 L700 8 L700 44 Z" fill="var(--teal)"/>
  </svg>
</section>

<section class="card card--front" aria-label="Card front">
  <div class="brand">
    <div class="brand__mark"><span class="brand__dot"></span>Meadowlight Soaps</div>
    <p class="brand__tagline">Creating Quality Handcrafted<br>Soaps &amp; Bath Products</p>
  </div>
  <div class="divider"></div>
  <div class="person">
    <p class="person__name">Carol Pritchett</p>
    <p class="person__role">OWNER/CREATOR</p>
  </div>
  <ul class="contact">
    <li class="contact__item">
      <svg class="contact__icon" viewBox="0 0 22 22" aria-hidden="true"><circle cx="11" cy="11" r="11" fill="var(--teal)"/><path d="M7 6h3l1 3-1.5 1a7 7 0 0 0 3 3l1-1.5 3 1v3c-6 0-10-4-10-10z" fill="#fff"/></svg>
      519.402.6183
    </li>
    <li class="contact__item">
      <svg class="contact__icon" viewBox="0 0 22 22" aria-hidden="true"><circle cx="11" cy="11" r="11" fill="var(--teal)"/><path d="M8 14l6-6M9.5 9.5l-2 2a2 2 0 0 0 3 3l2-2M12.5 12.5l2-2a2 2 0 0 0-3-3l-2 2" stroke="#fff" stroke-width="1.6" fill="none"/></svg>
      www.meadowlightsoaps.ca
    </li>
    <li class="contact__item">
      <svg class="contact__icon" viewBox="0 0 22 22" aria-hidden="true"><circle cx="11" cy="11" r="11" fill="var(--teal)"/></svg>
      friendpage.com/MeadowlightSoapandBath
    </li>
    <li class="contact__item">
      <svg class="contact__icon" viewBox="0 0 22 22" aria-hidden="true"><circle cx="11" cy="11" r="11" fill="var(--teal)"/><path d="M11 5a4 4 0 0 1 4 4c0 3-4 8-4 8s-4-5-4-8a4 4 0 0 1 4-4z" fill="#fff"/><circle cx="11" cy="9" r="1.5" fill="var(--teal)"/></svg>
      48 Fenwick Rd, Guelph, Ont N4K 2P9
    </li>
  </ul>
  <svg class="card__trim" viewBox="0 0 700 60" aria-hidden="true">
    <path d="M0 44 L700 44 L700 60 L0 60 Z" fill="var(--sand)"/>
    <path d="M520 44 C560 44 570 8 620 8 L700 8 L700 44 Z" fill="var(--teal)"/>
  </svg>
</section>

</body>
</html>
```